Modern Verdell Tree Care Website

I need a website for a full service Tree Care company. The company provides tree pruning, tree removal, tree preservation, emergency services, stump grinding, and emergency tree services.

Target Market(s)

Customers that need tree services

Industry/Entity Type

Landscaping, Tree Services

Coding

Coded - Design and coding required

Number of Pages Required

5+ page

Font styles to use
Sans Serif

Requirements
Must have
• Good clean design that showcases the services the company provides.
Nice to have
• Services page; contact form, blog, home page, about page

```html
<!DOCTYPE html>
<html lang="en">
<head>
<meta charset="utf-8">
<title>Verdell Tree Care</title>
<link href="https://fonts.googleapis.com/css2?family=Barlow:wght@400;500;600;700;800&display=swap" rel="stylesheet">
<style>
:root{
  --green:#6aa51e;
  --green-dark:#2f5a0c;
  --green-deep:#142a08;
  --orange:#f7931e;
  --ink:#1d1d1b;
  --muted:#5c5c5c;
  --tint:#eef2e2;
  --paper:#f6f7f1;
  --white:#ffffff;
}
*{margin:0;padding:0;box-sizing:border-box}
html,body{width:1200px;height:4518px;overflow:hidden;background:var(--white)}
body{font-family:"Barlow",sans-serif;color:var(--ink);position:relative}
.abs{position:absolute}
.photo{position:absolute}
.label{position:absolute;font-size:16px;font-weight:500;color:var(--green);letter-spacing:.5px;text-transform:uppercase}
.heading{position:absolute;font-size:36px;font-weight:700;line-height:1.05;color:var(--ink)}
.btn{position:absolute;display:flex;align-items:center;justify-content:center;background:var(--orange);color:var(--white);font-size:15px;font-weight:500}
.text{position:absolute;font-size:13.5px;line-height:22.5px;color:var(--muted)}

.brand{position:absolute;display:flex;align-items:center;gap:12px}
.brand-mark{width:30px;height:30px;background:var(--green)}
.brand-name{font-size:26px;font-weight:700;color:var(--ink);letter-spacing:.5px;line-height:1}
.phone{position:absolute;display:flex;align-items:center;gap:8px}
.phone-icon{width:40px;height:34px;border-radius:50%;background:#e3ecd4;display:flex;align-items:center;justify-content:center}
.phone b{display:block;font-size:15px;font-weight:600;color:var(--ink)}
.phone span{display:block;font-size:12px;color:#9a9a9a;line-height:1}
.navbar{position:absolute;left:368px;top:58px;width:832px;height:47px;background:var(--green);clip-path:polygon(40px 0,100% 0,100% 100%,0 100%)}
.nav{position:absolute;top:58px;height:47px;display:flex;align-items:center;font-size:13.5px;color:var(--white)}
.nav-home{left:447px;width:123px;background:var(--orange);justify-content:center;clip-path:polygon(28px 0,100% 0,calc(100% - 28px) 100%,0 100%)}

.hero{left:0;top:105px;width:1200px;height:543px;background:linear-gradient(110deg,#1f3a12 0%,#2f4d1c 45%,#4b5e3a 70%,#2a421a 100%)}
.hero-title{position:absolute;left:108px;top:243px;font-size:51px;font-weight:800;line-height:50px;color:var(--white);text-transform:uppercase;letter-spacing:.5px}
.hero-sub{position:absolute;left:108px;top:410px;font-size:17px;color:var(--white)}

.services-band{left:0;top:1340px;width:1200px;height:526px;background:var(--tint)}
.service-card{position:absolute;top:1549px;width:144px;height:241px;background:#f7f8f3;display:flex;flex-direction:column;align-items:center}
.service-card.active{background:linear-gradient(135deg,#8ec63f,#3f7d10)}
.service-icon{margin-top:50px;width:90px;height:90px;border-radius:50%;background:var(--white);display:flex;align-items:center;justify-content:center;box-shadow:0 2px 6px rgba(0,0,0,.08)}
.service-name{margin-top:24px;font-size:16px;font-weight:600;text-align:center;line-height:17px;color:var(--ink)}
.service-card.active .service-name{color:var(--white)}

.check{position:absolute;display:flex;align-items:center;gap:10px;font-size:12.5px;font-weight:500;color:var(--ink)}

.portfolio-band{left:0;top:2733px;width:1200px;height:640px;background:var(--green-dark)}

.testimonial-band{left:0;top:3373px;width:1200px;height:685px;background:var(--paper)}
.card{position:absolute;top:3600px;width:478px;height:286px;background:var(--white);box-shadow:0 2px 10px rgba(0,0,0,.04)}
.quote-mark{position:absolute;left:38px;top:28px;font-size:40px;font-weight:800;color:var(--green);line-height:1}
.card p{position:absolute;left:38px;top:80px;width:405px;font-size:13px;line-height:22px;color:var(--muted)}
.avatar{position:absolute;left:38px;top:190px;width:56px;height:56px;border-radius:50%;background:linear-gradient(135deg,#c9b8a4,#4a3d33)}
.person{position:absolute;left:110px;top:203px}
.person b{display:block;font-size:14px;font-weight:700}
.person span{display:block;font-size:12px;color:#888;line-height:1}
.dot{position:absolute;top:3914px;width:7px;height:7px;border-radius:50%;background:#d4d8cc}

.footer{left:0;top:4058px;width:1200px;height:460px;background:var(--green-deep)}
.cta{left:107px;top:3998px;width:983px;height:132px;background:var(--green)}
.cta-title{position:absolute;left:163px;top:4033px;font-size:29px;font-weight:700;line-height:35px;color:var(--white)}
.cta-btn{position:absolute;top:4040px;width:154px;height:49px;display:flex;align-items:center;justify-content:center;font-size:16px;font-weight:500}
.footer-head{position:absolute;top:4200px;font-size:16px;font-weight:600;color:var(--white)}
.footer-links{position:absolute;top:4252px;list-style:none;font-size:12.5px;line-height:30px;color:#d6dccd}
.footer-phone{position:absolute;left:848px;display:flex;align-items:center;gap:8px}
.footer-phone b{display:block;font-size:16px;font-weight:600;color:var(--white)}
.footer-phone span{display:block;font-size:12px;color:#8a9580;line-height:1}
.copyright{position:absolute;left:0;top:4486px;width:1200px;text-align:center;font-size:11px;color:#a6ad9c}
</style>
</head>
<body>

<div class="brand" style="left:108px;top:36px">
  <div class="brand-mark"></div>
  <div class="brand-name">Verdell Tree Care</div>
</div>
<div class="phone" style="left:715px;top:10px">
  <div class="phone-icon"><svg width="20" height="20" viewBox="0 0 24 24" fill="none" stroke="#6aa51e" stroke-width="2"><path d="M5 3h4l2 5-3 2a12 12 0 0 0 6 6l2-3 5 2v4a2 2 0 0 1-2 2A18 18 0 0 1 3 5a2 2 0 0 1 2-2z"/></svg></div>
  <div><b>(555) 214-3870</b><span>Phone</span></div>
</div>
<div class="phone" style="left:918px;top:10px">
  <div class="phone-icon"><svg width="20" height="20" viewBox="0 0 24 24" fill="none" stroke="#6aa51e" stroke-width="2"><path d="M5 3h4l2 5-3 2a12 12 0 0 0 6 6l2-3 5 2v4a2 2 0 0 1-2 2A18 18 0 0 1 3 5a2 2 0 0 1 2-2z"/></svg></div>
  <div><b>(555) 806-4412</b><span>Phone</span></div>
</div>
<div class="navbar"></div>
<div class="nav nav-home">Home</div>
<div class="nav" style="left:580px">About Us</div>
<div class="nav" style="left:686px">Services</div>
<div class="nav" style="left:789px">Portfolio</div>
<div class="nav" style="left:893px">Testimonials</div>
<div class="nav" style="left:1023px">Contact Us</div>

<div class="photo hero" role="img" aria-label="Arborist in a bucket lift cutting a pine tree with a chainsaw"></div>
<div class="hero-title">Transforming<br>Landscapes One<br>Tree At A Time</div>
<div class="hero-sub">Your Trusted Partner for Expert Tree Care Services</div>
<div class="btn" style="left:108px;top:461px;width:129px;height:42px">Get Started</div>
<svg class="abs" style="left:0;top:590px" width="1200" height="60" viewBox="0 0 1200 60">
  <polygon points="0,10 64,52 1128,52 1200,10 1200,60 0,60" fill="#fff"/>
  <polyline points="0,8 66,58 1126,58 1200,8" fill="none" stroke="#8cc43c" stroke-width="4"/>
</svg>

<div class="label" style="left:108px;top:826px">About Us</div>
<div class="heading" style="left:108px;top:851px;font-size:35px">Who We Are</div>
<div class="text" style="left:108px;top:898px;width:455px">At Verdell Tree Care, we are more than just a tree service company, we are stewards of our beautiful trees. With a passion deeply rooted in arboriculture, we embark on a mission to promote the health, beauty, and safety of your trees and landscapes.</div>
<div class="text" style="left:108px;top:1004px;width:455px">Whether it's expert tree trimming to enhance aesthetics, meticulous tree removal to mitigate hazards, or comprehensive tree health assessments to ensure safety, we approach each task with unwavering dedication and attention to detail.</div>
<div class="btn" style="left:108px;top:1127px;width:122px;height:38px;font-size:13px">Learn More</div>
<div class="photo" style="left:610px;top:727px;width:590px;height:400px;background:linear-gradient(120deg,#e8742a 0%,#c65a1c 30%,#8a9a2a 55%,#4e6a1c 100%)" role="img" aria-label="Arborist in orange gear trimming a shrub with pruning shears"></div>
<div class="photo" style="left:604px;top:1072px;width:213px;height:201px;background:#fff"></div>
<div class="photo" style="left:610px;top:1078px;width:201px;height:189px;background:linear-gradient(135deg,#7a6a58,#3d3a30)" role="img" aria-label="Climber cutting a tree trunk with a chainsaw"></div>
<div class="photo" style="left:825px;top:1144px;width:165px;height:123px;background:linear-gradient(160deg,#7fa35a,#3d5d22)" role="img" aria-label="Bucket truck working among tall trees"></div>
<div class="photo" style="left:1004px;top:1144px;width:165px;height:123px;background:linear-gradient(160deg,#93a87a,#4c5a36)" role="img" aria-label="Worker cutting branches high in a tree"></div>

<div class="abs services-band"></div>
<div class="label" style="left:0;width:1200px;text-align:center;top:1413px">Our Services</div>
<div class="heading" style="left:0;width:1200px;text-align:center;top:1446px">Explore Our Comprehensive<br>Tree Care Solutions</div>

<div class="service-card" style="left:108px"><div class="service-icon"><svg width="44" height="44" viewBox="0 0 44 44" fill="none" stroke="#6aa51e" stroke-width="1.8"><circle cx="22" cy="14" r="9"/><path d="M22 23v15M14 38h16M8 30l8-4"/></svg></div><div class="service-name">Tree<br>Pruning</div></div>
<div class="service-card" style="left:275px"><div class="service-icon"><svg width="44" height="44" viewBox="0 0 44 44" fill="none" stroke="#6aa51e" stroke-width="1.8"><rect x="6" y="24" width="30" height="9" rx="4"/><circle cx="36" cy="28.5" r="4.5"/><path d="M16 24v-10M12 14h8"/></svg></div><div class="service-name">Tree<br>Removal</div></div>
<div class="service-card active" style="left:443px"><div class="service-icon"><svg width="44" height="44" viewBox="0 0 44 44" fill="none" stroke="#6aa51e" stroke-width="1.8"><circle cx="22" cy="13" r="8"/><path d="M22 21v10M8 30c6 0 8 6 14 6s10-4 16-8"/></svg></div><div class="service-name">Tree<br>Preservation</div></div>
<div class="service-card" style="left:610px"><div class="service-icon"><svg width="44" height="44" viewBox="0 0 44 44" fill="none" stroke="#6aa51e" stroke-width="1.8"><path d="M22 5l8 11h-5l7 9h-6l8 10H10l8-10h-6l7-9h-5z M22 35v5"/></svg></div><div class="service-name">Emergency<br>Services</div></div>
<div class="service-card" style="left:778px"><div class="service-icon"><svg width="44" height="44" viewBox="0 0 44 44" fill="none" stroke="#6aa51e" stroke-width="1.8"><path d="M8 36h28M14 36v-10h16v10M18 26v-10M26 26v-14M22 26v-18"/></svg></div><div class="service-name">Stump<br>Grinding</div></div>
<div class="service-card" style="left:946px"><div class="service-icon"><svg width="44" height="44" viewBox="0 0 44 44" fill="none" stroke="#6aa51e" stroke-width="1.8"><path d="M6 36h32M12 36V22M12 22l-5-6h10zM28 36V18M28 18l-6-8h12z M16 10h8M4 14h6"/></svg></div><div class="service-name">Storm Damage<br>Cleanup</div></div>

<div class="photo" style="left:108px;top:1941px;width:419px;height:496px;background:linear-gradient(160deg,#9aa07a 0%,#6b6a48 45%,#c0623a 60%,#4a4a36 100%)" role="img" aria-label="Arborist in helmet and harness cutting a tree limb with a chainsaw"></div>
<div class="photo" style="left:140px;top:2497px;width:370px;height:236px;background:radial-gradient(ellipse at 50% 40%,#eceeea 0%,#f7f8f6 60%,#ffffff 100%)" role="img" aria-label="Faint line sketch of a spreading tree"></div>
<div class="label" style="left:606px;top:1966px">Verdell Tree Care</div>
<div class="heading" style="left:606px;top:1991px;font-size:35px">Why Choose Us?</div>
<div class="text" style="left:606px;top:2033px;width:470px;font-size:13px;line-height:22.5px">From our unwavering commitment to excellence to our dedication to preserving the natural beauty of your landscape, discover why Verdell Tree Care stands out as the premier choice for all your tree care needs.</div>

<div class="check" style="left:606px;top:2115px"><svg width="20" height="20" viewBox="0 0 20 20"><path d="M2 10l6 6L18 3" fill="none" stroke="#6aa51e" stroke-width="3"/></svg>Licensed and Insured</div>
<div class="check" style="left:818px;top:2115px"><svg width="20" height="20" viewBox="0 0 20 20"><path d="M2 10l6 6L18 3" fill="none" stroke="#6aa51e" stroke-width="3"/></svg>24-Hours Emergency Services</div>
<div class="check" style="left:606px;top:2154px"><svg width="20" height="20" viewBox="0 0 20 20"><path d="M2 10l6 6L18 3" fill="none" stroke="#6aa51e" stroke-width="3"/></svg>Professional Work</div>
<div class="check" style="left:818px;top:2154px"><svg width="20" height="20" viewBox="0 0 20 20"><path d="M2 10l6 6L18 3" fill="none" stroke="#6aa51e" stroke-width="3"/></svg>Locally Owned &amp; Operated</div>
<div class="check" style="left:606px;top:2192px"><svg width="20" height="20" viewBox="0 0 20 20"><path d="M2 10l6 6L18 3" fill="none" stroke="#6aa51e" stroke-width="3"/></svg>Free Estimates</div>
<div class="check" style="left:818px;top:2192px"><svg width="20" height="20" viewBox="0 0 20 20"><path d="M2 10l6 6L18 3" fill="none" stroke="#6aa51e" stroke-width="3"/></svg>Safety is Our No.1 Priority</div>
<div class="check" style="left:606px;top:2231px"><svg width="20" height="20" viewBox="0 0 20 20"><path d="M2 10l6 6L18 3" fill="none" stroke="#6aa51e" stroke-width="3"/></svg>Licensed Arborist on Staff</div>

<div class="photo" style="left:610px;top:2307px;width:480px;height:349px;background:linear-gradient(160deg,#5e8a2e 0%,#7fa843 50%,#b3b78f 75%,#6e9838 100%)" role="img" aria-label="Green stump grinder chipping a stump on a lawn"></div>

<div class="abs portfolio-band"></div>
<div class="label" style="left:106px;top:2802px;color:#fff">Our Portfolio</div>
<div class="heading" style="left:106px;top:2832px;color:#fff">Worked We Have Done</div>
<div class="btn" style="left:941px;top:2817px;width:145px;height:49px;font-size:16px">More Projects</div>
<div class="photo" style="left:107px;top:2915px;width:483px;height:184px;background:linear-gradient(120deg,#2f6a14,#6aa33a 60%,#e8d4c0)" role="img" aria-label="Hands trimming a hedge with shears"></div>
<div class="photo" style="left:604px;top:2915px;width:233px;height:184px;background:linear-gradient(150deg,#8b8a6a,#4b4a3a)" role="img" aria-label="Chainsaw cutting a log"></div>
<div class="photo" style="left:853px;top:2915px;width:233px;height:184px;background:linear-gradient(180deg,#7ea3c8 0%,#5c8a3a 55%,#4a7a2a 100%)" role="img" aria-label="Crane truck removing a tree in a yard"></div>
<div class="photo" style="left:107px;top:3113px;width:231px;height:184px;background:linear-gradient(120deg,#8a5a3a,#c9a040 60%,#6a8a4a)" role="img" aria-label="Chainsaw notching a tree trunk"></div>
<div class="photo" style="left:354px;top:3113px;width:233px;height:184px;background:linear-gradient(160deg,#9a9488,#6a655a)" role="img" aria-label="Cut tree sections on a driveway"></div>
<div class="photo" style="left:601px;top:3113px;width:485px;height:184px;background:linear-gradient(120deg,#c98a4a,#8a6a48 50%,#d4b48a)" role="img" aria-label="Stump grinder wheel spraying wood chips"></div>

<div class="abs testimonial-band"></div>
<div class="label" style="left:0;width:1200px;text-align:center;top:3462px">Client Testimonials</div>
<div class="heading" style="left:0;width:1200px;text-align:center;top:3500px">See What Our Clients<br>Have to Say:</div>
<div class="card" style="left:105px">
  <div class="quote-mark">”</div>
  <p>I Was Amazed By The Professionalism And Efficiency Of The Verdell Tree Care Team. They Took Care Of A Hazardous Tree On My Property With Precision And Care. I Highly Recommend Their Services To Anyone In Need Of Expert Tree Care.</p>
  <div class="avatar" role="img" aria-label="Client portrait"></div>
  <div class="person"><b>Linda Marsh</b><span>Homeowner</span></div>
</div>
<div class="card" style="left:608px">
  <div class="quote-mark">”</div>
  <p>Choosing Verdell Tree Care Was The Best Decision I Made For My Property. Their Team Was Professional, Courteous, And Incredibly Skilled. They Transformed My Overgrown Trees Into A Beautifully Manicured Landscape. I Couldn't Be Happier With The Results.</p>
  <div class="avatar" role="img" aria-label="Client portrait"></div>
  <div class="person"><b>Marcus Whitley</b><span>Homeowner</span></div>
</div>
<div class="dot" style="left:551px"></div>
<div class="dot" style="left:571px"></div>
<div class="dot" style="left:591px;width:10px;height:10px;top:3912px;background:var(--green)"></div>
<div class="dot" style="left:614px"></div>
<div class="dot" style="left:634px"></div>

<div class="abs footer"></div>
<div class="abs cta"></div>
<div class="cta-title">Ready to Get Free Consultations<br>Any Kind Of It Solutions?</div>
<div class="cta-btn" style="left:708px;background:#fff;color:var(--green)">Get A Quote</div>
<div class="cta-btn" style="left:876px;border:2px solid #fff;color:#fff">Learn More</div>

<div class="brand" style="left:161px;top:4200px">
  <div class="brand-mark"></div>
  <div class="brand-name" style="color:#fff">Verdell Tree Care</div>
</div>
<div class="footer-head" style="left:445px">Quick Links</div>
<ul class="footer-links" style="left:445px"><li>Home</li><li>About Us</li><li>Services</li><li>Portfolio</li><li>Testimonials</li><li>Contact Us</li></ul>
<div class="footer-head" style="left:620px">Services</div>
<ul class="footer-links" style="left:620px"><li>Tree Pruning</li><li>Tree Removal</li><li>Tree Preservation</li><li>Emergency Services</li><li>Stump Grinding</li><li>Emergency Tree Services</li></ul>
<div class="footer-head" style="left:848px">Contact Info</div>
<div class="footer-phone" style="top:4252px">
  <div class="phone-icon" style="background:#24391a"><svg width="20" height="20" viewBox="0 0 24 24" fill="none" stroke="#6aa51e" stroke-width="2"><path d="M5 3h4l2 5-3 2a12 12 0 0 0 6 6l2-3 5 2v4a2 2 0 0 1-2 2A18 18 0 0 1 3 5a2 2 0 0 1 2-2z"/></svg></div>
  <div><b>(555) 214-3870</b><span>Phone</span></div>
</div>
<div class="footer-phone" style="top:4320px">
  <div class="phone-icon" style="background:#24391a"><svg width="20" height="20" viewBox="0 0 24 24" fill="none" stroke="#6aa51e" stroke-width="2"><path d="M5 3h4l2 5-3 2a12 12 0 0 0 6 6l2-3 5 2v4a2 2 0 0 1-2 2A18 18 0 0 1 3 5a2 2 0 0 1 2-2z"/></svg></div>
  <div><b>(555) 806-4412</b><span>Phone</span></div>
</div>
<div class="copyright">© 2024 Verdell Tree Care. All Rights Reserved.</div>

</body>
</html>
```